Bluecrest Learning Corps by graduating students from college in two years

Based on the logo design, create stationary and business cards for
Dr. Venrel T Oskamp, CEO, (703) 482-1736
and Marisa Deltoft, Respresentative, (301) 647-2208
Address: 4719 Pellham Court, Glenmore Station, VA 22187
Incorporate elelments of the logo

Target Market(s)

USA

Font styles to use
Other font styles liked:
• match with the logo type style

```html
<!DOCTYPE html>
<html lang="en">
<head>
<meta charset="utf-8">
<title>Bluecrest Learning Corps – Business Card</title>
<link href="https://fonts.googleapis.com/css2?family=Poppins:wght@400;700&display=swap" rel="stylesheet">
<style>
  :root {
    --navy: #0a2260;
    --navy-deep: #071a4d;
    --gold: #f4c230;
    --white: #ffffff;
    --ink: #141414;
    --backdrop: #9c9c9c;
  }
  * { margin: 0; padding: 0; box-sizing: border-box; }
  html, body { width: 1200px; height: 1083px; overflow: hidden; }
  body {
    background: var(--backdrop);
    font-family: "Poppins", sans-serif;
    position: relative;
  }
  .card {
    position: absolute;
    left: 220px;
    width: 760px;
    height: 434px;
    overflow: hidden;
    border-bottom: 3px solid var(--gold);
  }
  .card--front { top: 60px; background: var(--white); }
  .card--back { top: 568px; background: var(--navy); }

  .front__wave { position: absolute; left: 0; bottom: 0; width: 760px; height: 434px; }

  .brand {
    position: absolute;
    display: flex;
    align-items: center;
    gap: 12px;
  }
  .brand__dot { width: 22px; height: 22px; border-radius: 50%; background: var(--gold); flex: none; }
  .brand__name { font-weight: 700; line-height: 1.15; }

  .card--front .brand { left: 52px; top: 110px; width: 290px; }
  .card--front .brand__name { color: var(--navy); font-size: 25px; }

  .front__divider {
    position: absolute;
    left: 368px; top: 70px;
    width: 2px; height: 170px;
    background: var(--gold);
  }
  .contact { position: absolute; left: 396px; top: 72px; color: var(--ink); }
  .contact__name { color: var(--navy); font-weight: 700; font-size: 30px; line-height: 1.2; }
  .contact__title { font-size: 21px; margin-top: 2px; }
  .contact__phone { display: flex; align-items: center; gap: 8px; font-size: 21px; margin-top: 2px; }
  .contact__phone svg { width: 16px; height: 24px; flex: none; }
  .contact__address { font-size: 21px; margin-top: 18px; line-height: 1.35; font-style: normal; }

  .back__pattern {
    position: absolute; inset: 0;
    background: linear-gradient(135deg, #0d2a72 0%, var(--navy) 50%, var(--navy-deep) 100%);
  }
  .back__badge {
    position: absolute;
    left: 265px; top: 102px;
    width: 230px; height: 230px;
    border-radius: 50%;
    background: var(--white);
    border: 10px solid var(--gold);
    display: flex; align-items: center; justify-content: center;
    text-align: center;
    padding: 20px;
  }
  .back__badge .brand__name { color: var(--navy); font-size: 24px; }
</style>
</head>
<body>

  <section class="card card--front">
    <svg class="front__wave" viewBox="0 0 760 434" preserveAspectRatio="none" aria-hidden="true">
      <path d="M0,285 C120,330 260,385 460,395 C600,402 700,405 760,410 L760,434 L0,434 Z" fill="var(--gold)"/>
      <path d="M0,300 C110,350 250,402 460,410 C600,415 700,416 760,418 L760,434 L0,434 Z" fill="var(--navy)"/>
    </svg>

    <div class="brand">
      <span class="brand__dot"></span>
      <span class="brand__name">Bluecrest Learning Corps</span>
    </div>

    <div class="front__divider"></div>

    <div class="contact">
      <h1 class="contact__name">Dr. Venrel T Oskamp</h1>
      <p class="contact__title">Chief Executive Officer</p>
      <p class="contact__phone">
        <svg viewBox="0 0 16 24" aria-hidden="true">
          <rect x="1.5" y="1.5" width="13" height="21" rx="2.5" fill="none" stroke="var(--gold)" stroke-width="2"/>
          <circle cx="8" cy="18.5" r="1.4" fill="var(--gold)"/>
        </svg>
        (703) 482-1736
      </p>
      <address class="contact__address">4719 Pellham Court<br>Glenmore Station, VA 22187</address>
    </div>
  </section>

  <section class="card card--back">
    <div class="back__pattern" role="img" aria-label="Faint repeating binary-digit pattern in lighter navy across the card back"></div>
    <div class="back__badge">
      <div class="brand">
        <span class="brand__name">Bluecrest Learning Corps</span>
      </div>
    </div>
  </section>

</body>
</html>
```